I need email signatures for my admin staff members
info:
Teresa Volkaric
Support Coordinator
Unit 4, 517 Marden Vale Road, Quillby NSW 2185
Tel: 02 94637215 Mob: 0417582946
email: teresa.vo@kindwayservices.com
www.kindwayservices.com

Target Market(s)

community services industry

Industry/Entity Type

Community Service

Requirements
Must have
• Specialist Provider of Multicultural Support Services
Nice to have
• "I acknowledge the traditional owners of the land on which we live, work and dream"
plus their flags as attached

```html
<!DOCTYPE html>
<html lang="en">
<head>
<meta charset="utf-8">
<title>Email Signature – Teresa Volkaric</title>
<link href="https://fonts.googleapis.com/css2?family=Lato:ital,wght@0,400;0,700;1,400&display=swap" rel="stylesheet">
<style>
  :root {
    --orange: #f7931e;
    --charcoal: #333333;
    --ink: #222222;
    --paper: #ffffff;
    --backdrop: #dcdcdc;
    --flag-red: #d8101e;
    --flag-black: #111111;
    --ts-green: #1fbf2f;
    --ts-blue: #1f3fd0;
  }
  * { box-sizing: border-box; margin: 0; padding: 0; }
  html, body {
    width: 1200px; height: 794px; overflow: hidden;
    background: var(--backdrop);
    font-family: "Lato", sans-serif;
    color: var(--ink);
  }
  .signature {
    position: absolute; left: 50px; top: 190px;
    width: 1100px; height: 413px;
    background: var(--paper);
  }
  .side-band {
    position: absolute; left: 0; top: 0; bottom: 0; width: 58px;
    background: var(--charcoal);
  }
  .person { position: absolute; left: 73px; top: 46px; }
  .person-name {
    font-size: 35px; font-weight: 700; color: var(--orange);
    line-height: 1.05; letter-spacing: 0.2px;
  }
  .person-role { font-size: 26px; line-height: 1.15; margin-left: 2px; }
  .acknowledgement {
    position: absolute; left: 478px; top: 46px;
    font-size: 22px; line-height: 28px; color: var(--ink);
  }
  .flags { position: absolute; left: 922px; top: 65px; display: flex; gap: 3px; }
  .flag-area { width: 62px; height: 42px; }
  .flag-area.first-nations {
    background: linear-gradient(180deg, var(--flag-black) 0%, var(--flag-black) 35%, var(--flag-red) 65%, var(--flag-red) 100%);
  }
  .flag-area.islander {
    background: linear-gradient(180deg, var(--ts-green) 0%, var(--ts-blue) 30%, var(--ts-blue) 70%, var(--ts-green) 100%);
  }
  .divider {
    position: absolute; left: 58px; top: 137px; width: 989px; height: 3px;
    background: var(--orange);
  }
  .contact-icons { position: absolute; left: 8px; top: 0; }
  .contact-icon { position: absolute; left: 0; width: 34px; height: 34px; }
  .contact-list { position: absolute; left: 70px; top: 0; list-style: none; }
  .contact-item {
    position: absolute; left: 0; white-space: nowrap;
    font-size: 26px; line-height: 34px;
  }
  .contact-item.address { font-size: 28px; left: 2px; }
  .brand {
    position: absolute; left: 708px; top: 152px; width: 360px;
    text-align: center;
  }
  .brand-mark {
    width: 104px; height: 104px; border-radius: 50%;
    background: var(--orange); margin: 0 auto 14px;
  }
  .brand-name {
    font-size: 28px; font-weight: 700; color: var(--orange);
    letter-spacing: 1.5px; line-height: 1;
  }
  .brand-tagline {
    margin-top: 16px; font-size: 22px; font-style: italic;
    color: var(--orange); line-height: 28px;
  }
</style>
</head>
<body>
  <section class="signature">
    <div class="side-band"></div>

    <div class="person">
      <p class="person-name">Teresa Volkaric</p>
      <p class="person-role">Support Coordinator</p>
    </div>

    <p class="acknowledgement">“I acknowledge the traditional owners of the<br>land on&nbsp; which we live, work and dream”</p>

    <div class="flags">
      <div class="flag-area first-nations" role="img" aria-label="Aboriginal flag"></div>
      <div class="flag-area islander" role="img" aria-label="Torres Strait Islander flag"></div>
    </div>

    <div class="divider"></div>

    <div class="contact-icons">
      <svg class="contact-icon" style="top:189px" viewBox="0 0 34 34" aria-hidden="true">
        <circle cx="17" cy="17" r="17" fill="var(--orange)"/>
        <path d="M11 9c1-1 2-1 3 0l2 3c.6 1 .4 1.8-.3 2.5l-1 1c1 2 2.6 3.6 4.6 4.6l1-1c.7-.7 1.5-.9 2.5-.3l3 2c1 1 1 2 0 3l-1.5 1.5c-5 1-14-8-13-13z" fill="var(--paper)"/>
      </svg>
      <svg class="contact-icon" style="top:227px" viewBox="0 0 34 34" aria-hidden="true">
        <circle cx="17" cy="17" r="17" fill="var(--orange)"/>
        <rect x="11" y="8" width="12" height="18" rx="2" fill="none" stroke="var(--paper)" stroke-width="2.4"/>
        <line x1="11" y1="22" x2="23" y2="22" stroke="var(--paper)" stroke-width="2"/>
      </svg>
      <svg class="contact-icon" style="top:267px" viewBox="0 0 34 34" aria-hidden="true">
        <circle cx="17" cy="17" r="17" fill="var(--orange)"/>
        <rect x="8" y="11" width="18" height="12" fill="none" stroke="var(--paper)" stroke-width="2"/>
        <path d="M8 11l9 7 9-7M8 23l7-6M26 23l-7-6" fill="none" stroke="var(--paper)" stroke-width="1.6"/>
      </svg>
      <svg class="contact-icon" style="top:303px" viewBox="0 0 34 34" aria-hidden="true">
        <circle cx="17" cy="17" r="17" fill="var(--orange)"/>
        <circle cx="17" cy="17" r="10" fill="none" stroke="var(--paper)" stroke-width="2.2"/>
        <ellipse cx="17" cy="17" rx="4.5" ry="10" fill="none" stroke="var(--paper)" stroke-width="1.6"/>
        <line x1="7" y1="17" x2="27" y2="17" stroke="var(--paper)" stroke-width="1.6"/>
      </svg>
      <svg class="contact-icon" style="top:349px" viewBox="0 0 34 34" aria-hidden="true">
        <circle cx="17" cy="17" r="17" fill="var(--orange)"/>
        <path d="M17 7a7 7 0 0 1 7 7c0 5-7 13-7 13s-7-8-7-13a7 7 0 0 1 7-7z" fill="var(--paper)"/>
        <circle cx="17" cy="14" r="3" fill="var(--orange)"/>
      </svg>
    </div>

    <ul class="contact-list">
      <li class="contact-item" style="top:189px">02 94637215</li>
      <li class="contact-item" style="top:227px">0417582946</li>
      <li class="contact-item" style="top:267px">teresa.vo@kindwayservices.com</li>
      <li class="contact-item" style="top:303px">www.kindwayservices.com</li>
      <li class="contact-item address" style="top:349px">Unit 4, 517 Marden Vale Road, Quillby NSW 2185</li>
    </ul>

    <div class="brand">
      <div class="brand-mark"></div>
      <p class="brand-name">KINDWAY SERVICES</p>
      <p class="brand-tagline">Specialist Provider of&nbsp; Multicultural<br>Support Services</p>
    </div>
  </section>
</body>
</html>
```